The Linen Loft Co

We need a business card design for our wardrobe company.
Please visit our website www.gentlelinenlofts.com to get an idea of who we are.

```html
<!DOCTYPE html>
<html lang="en">
<head>
<meta charset="utf-8">
<title>The Linen Loft Co — Business Card</title>
<link rel="stylesheet" href="https://fonts.googleapis.com/css2?family=Open+Sans:wght@400;600;700&display=swap">
<style>
  :root {
    --backdrop: #d6d6d6;
    --card-white: #ffffff;
    --card-black: #000000;
    --ink: #111111;
    --ink-soft: #333333;
    --paper-text: #ffffff;
  }
  * { box-sizing: border-box; margin: 0; padding: 0; }
  html, body {
    width: 1200px;
    height: 900px;
    overflow: hidden;
    background: var(--backdrop);
    font-family: "Open Sans", Arial, sans-serif;
  }
  .stage {
    position: relative;
    width: 1200px;
    height: 900px;
  }
  .card {
    position: absolute;
    width: 540px;
    height: 310px;
    box-shadow: 0 6px 18px rgba(0,0,0,0.18);
    overflow: hidden;
  }
  .card--front { left: 40px; top: 470px; background: var(--card-white); color: var(--ink); }
  .card--back  { left: 620px; top: 120px; background: var(--card-black); color: var(--paper-text); }

  .brand {
    position: absolute;
    display: flex;
    align-items: center;
    gap: 10px;
  }
  .brand__mark {
    width: 46px;
    height: 34px;
    border: 2px solid currentColor;
    flex: none;
  }
  .brand__name {
    font-size: 11px;
    font-weight: 600;
    letter-spacing: 0.12em;
    text-transform: uppercase;
    line-height: 1.3;
    white-space: nowrap;
  }
  .brand__tagline {
    font-size: 11px;
    font-weight: 600;
    letter-spacing: 0.02em;
    line-height: 1.3;
    white-space: nowrap;
  }
  .card--front .brand { left: 34px; top: 40px; }
  .card--back .brand { left: 130px; top: 120px; }
  .card--back .brand__mark { width: 70px; height: 52px; }
  .card--back .brand__name,
  .card--back .brand__tagline { font-size: 14px; }

  .contact {
    position: absolute;
    left: 300px;
    top: 120px;
    font-size: 13px;
    line-height: 1.35;
    color: var(--ink-soft);
  }
  .contact__name {
    font-size: 17px;
    font-weight: 700;
    letter-spacing: 0.04em;
    color: var(--ink);
  }
  .contact__title { margin-bottom: 14px; }
  .contact__address { margin-bottom: 14px; }

  .accent-bar {
    position: absolute;
    left: 160px;
    bottom: 0;
    width: 110px;
    height: 24px;
    background: var(--card-black);
  }
</style>
</head>
<body>
  <main class="stage">
    <section class="card card--back" aria-label="Business card back">
      <div class="brand">
        <span class="brand__mark" aria-hidden="true"></span>
        <div>
          <p class="brand__name">The Linen Loft Co</p>
          <p class="brand__tagline">Crafted for Calm Spaces</p>
        </div>
      </div>
    </section>

    <section class="card card--front" aria-label="Business card front">
      <div class="brand">
        <span class="brand__mark" aria-hidden="true"></span>
        <div>
          <p class="brand__name">The Linen Loft Co</p>
          <p class="brand__tagline">Crafted for Calm Spaces</p>
        </div>
      </div>
      <div class="contact">
        <p class="contact__name">YOUR NAME</p>
        <p class="contact__title">Your Title</p>
        <p class="contact__address">Your address<br>city, state, ZIP 0000</p>
        <p>P: 123-456-2100</p>
        <p>yourmail@linenmail.com</p>
        <p>www.yourwebsite.com</p>
      </div>
      <span class="accent-bar" aria-hidden="true"></span>
    </section>
  </main>
</body>
</html>
```